New Company Business Card design

Looking for a corporate looking business card utilising my new logo design - the logo i would like embossed as one option and flat as another - simplistic but stylish - less is more - we are an import export business launching into the market - i would like a couple of options as main background - Grey or Black

```html
<!DOCTYPE html>
<html lang="en">
<head>
<meta charset="utf-8">
<title>Meridian Trade Partners – Business Card</title>
<link href="https://fonts.googleapis.com/css2?family=Roboto:wght@400;500&display=swap" rel="stylesheet">
<style>
  :root {
    --backdrop: #e4e2df;
    --card: #fbfbfa;
    --brand-blue: #1f6fb8;
    --text-grey: #5a5a5a;
    --icon-blue: #1f6fb8;
    --card-shadow: rgba(0, 0, 0, 0.18);
  }
  * { margin: 0; padding: 0; box-sizing: border-box; }
  html, body {
    width: 1200px;
    height: 848px;
    overflow: hidden;
    background: var(--backdrop);
    font-family: "Roboto", Arial, sans-serif;
  }
  .canvas {
    position: relative;
    width: 1200px;
    height: 848px;
  }
  .card {
    position: absolute;
    width: 600px;
    height: 343px;
    background: var(--card);
    box-shadow: 0 6px 18px var(--card-shadow);
    overflow: hidden;
  }
  .card--front { left: 110px; top: 70px; }
  .card--back  { left: 490px; top: 435px; }

  .wordmark {
    color: var(--brand-blue);
    font-weight: 500;
    display: flex;
    align-items: center;
  }
  .wordmark__dot {
    border-radius: 50%;
    background: var(--brand-blue);
    flex: none;
  }
  .card--front .wordmark {
    position: absolute;
    left: 0; right: 0; top: 0; bottom: 0;
    justify-content: center;
    gap: 14px;
    font-size: 30px;
    letter-spacing: 1px;
  }
  .card--front .wordmark__dot { width: 22px; height: 22px; }

  .card--back .wordmark {
    position: absolute;
    right: 42px;
    top: 38px;
    gap: 10px;
    font-size: 40px;
    letter-spacing: 2px;
  }
  .card--back .wordmark__dot { width: 26px; height: 26px; }

  .contact {
    position: absolute;
    left: 42px;
    bottom: 28px;
    color: var(--text-grey);
    font-size: 14px;
    line-height: 18px;
  }
  .contact__name {
    color: var(--brand-blue);
    font-weight: 500;
    font-size: 19px;
    line-height: 22px;
    letter-spacing: 0.5px;
  }
  .contact__role { margin-bottom: 8px; }
  .contact__address { margin-bottom: 8px; }
  .contact__list { list-style: none; }
  .contact__list li {
    display: flex;
    align-items: center;
    gap: 10px;
  }
  .contact__list svg {
    width: 12px;
    height: 12px;
    fill: var(--icon-blue);
    flex: none;
  }
</style>
</head>
<body>
<main class="canvas">

  <section class="card card--front" aria-label="Card front">
    <div class="wordmark">
      <span class="wordmark__dot"></span>
      <span class="wordmark__name">MERIDIAN TRADE PARTNERS</span>
    </div>
  </section>

  <section class="card card--back" aria-label="Card back">
    <div class="wordmark">
      <span class="wordmark__dot"></span>
      <span class="wordmark__name">MTP</span>
    </div>

    <div class="contact">
      <p class="contact__name">DANIEL HART</p>
      <p class="contact__role">CEO/FOUNDER</p>
      <p class="contact__address">214 Harbor View Road<br>Juneau, Alaska 99801</p>
      <ul class="contact__list">
        <li>
          <svg viewBox="0 0 12 12" aria-hidden="true"><path d="M2.5 0.5 L4.5 0.5 L5.2 3.2 L3.8 4.3 Q5 6.8 7.7 8.2 L8.8 6.8 L11.5 7.5 L11.5 9.5 Q11 11.5 9 11.5 Q1 10.5 0.5 3 Q0.5 1 2.5 0.5 Z"/></svg>
          <span>907 555 0142</span>
        </li>
        <li>
          <svg viewBox="0 0 12 12" aria-hidden="true"><path d="M3 0 H9 Q10 0 10 1 V11 Q10 12 9 12 H3 Q2 12 2 11 V1 Q2 0 3 0 Z M3.2 1.5 V9.5 H8.8 V1.5 Z M5.4 10.2 H6.6 V11.2 H5.4 Z"/></svg>
          <span>907 555 0187</span>
        </li>
        <li>
          <svg viewBox="0 0 12 12" aria-hidden="true"><path d="M3 0 H9 V4 H3 Z M1 4.5 H11 Q12 4.5 12 5.5 V10 H0 V5.5 Q0 4.5 1 4.5 Z M3 8 H9 V12 H3 Z"/></svg>
          <span>907 555 0163</span>
        </li>
        <li>
          <svg viewBox="0 0 12 12" aria-hidden="true"><path d="M0 2 H12 V10 H0 Z M0.8 2.6 L6 6.6 L11.2 2.6 Z" fill-rule="evenodd"/></svg>
          <span>hello@meridiantrade.com</span>
        </li>
        <li>
          <svg viewBox="0 0 12 12" aria-hidden="true"><circle cx="6" cy="6" r="5.5"/></svg>
          <span>www.meridiantrade.com</span>
        </li>
      </ul>
    </div>
  </section>

</main>
</body>
</html>
```